Volbrey Inc Business Card

Looking to get an updated business card for a Contract Machining company (www.volbreyinc.example) - looking for a clean design the portrays the technical nature of the business - colors can follow the website design and be in any combination that makes sense (red black, white, metallic or silver) - logos attached for use also. Would like space for: Name, title, business phone (555 214-3086), cell phone , website (www.volbreyinc.example) - possibly QR code could be integrated for website (designer choice), business address - 418 Harlow Bend, Tallow Creek, QA 48199 (cards will be for 4 employees, I will either need to modify a template or I can provide individual information)
Target Market(s)
Aerospace, defense and medical device manufacturing companies that need machining
Industry/Entity Type
Machining for aerospace, defense, medical
Contact Information for Business Card
Name, Title, Business Phone, Cell Phone, email, business website and business address
Look and feel

```html
<!DOCTYPE html>
<html lang="en">
<head>
<meta charset="utf-8">
<title>Volbrey Inc Business Card</title>
<link rel="stylesheet" href="https://fonts.googleapis.com/css2?family=Poppins:wght@400;600;700;800&display=swap">
<style>
  :root {
    --brand-red: #b01e24;
    --deep-red: #72131a;
    --ink: #1b1b1b;
    --paper: #ffffff;
    --backdrop: #acacac;
    --rule: #9a9a9a;
  }
  * { box-sizing: border-box; margin: 0; padding: 0; }
  html, body {
    width: 1093px; height: 1200px; overflow: hidden;
    background: var(--backdrop);
    font-family: "Poppins", sans-serif;
  }
  .canvas { position: relative; width: 1093px; height: 1200px; }

  .card { position: absolute; left: 264px; width: 580px; height: 357px; overflow: hidden; }
  .card-front { top: 226px; background: var(--paper); }
  .card-back { top: 620px; width: 582px; background: var(--brand-red); display: flex; align-items: center; justify-content: center; }

  .brand-block { position: absolute; left: 95px; top: 79px; width: 152px; text-align: center; }
  .brand-disc { width: 152px; height: 152px; border-radius: 50%; background: var(--brand-red); margin: 0 auto; }
  .brand-name { margin-top: 8px; font-weight: 700; font-size: 20px; letter-spacing: 0.5px; color: var(--brand-red); white-space: nowrap; }

  .divider { position: absolute; left: 284px; top: 75px; width: 1px; height: 208px; background: var(--rule); }

  .details { position: absolute; left: 312px; top: 80px; color: var(--ink); }
  .person-name { font-weight: 700; font-size: 20.5px; line-height: 24px; color: var(--brand-red); letter-spacing: 0.2px; }
  .person-title { font-size: 16.5px; line-height: 20px; }

  .contact-list { list-style: none; margin-top: 14px; }
  .contact-list li { display: flex; align-items: center; font-size: 16.5px; line-height: 21px; height: 21px; white-space: nowrap; }
  .contact-list svg { width: 15px; height: 15px; margin-right: 7px; flex: none; fill: var(--brand-red); }
  .web-accent { color: var(--brand-red); }

  .address { margin-top: 13px; font-size: 16.5px; line-height: 21px; font-style: normal; }

  .bottom-band { position: absolute; left: 0; bottom: 0; width: 580px; height: 26px; }

  .back-wordmark { font-weight: 800; font-size: 78px; letter-spacing: 1px; color: var(--deep-red); line-height: 1; }
</style>
</head>
<body>
<main class="canvas">
  <section class="card card-front" aria-label="Business card front">
    <div class="brand-block">
      <div class="brand-disc"></div>
      <div class="brand-name">VOLBREY INC</div>
    </div>

    <div class="divider"></div>

    <div class="details">
      <h1 class="person-name">MARCUS ELLERY</h1>
      <p class="person-title">Managing Director</p>
      <ul class="contact-list">
        <li>
          <svg viewBox="0 0 24 24" aria-hidden="true"><path d="M6.6 10.8a15.1 15.1 0 0 0 6.6 6.6l2.2-2.2c.3-.3.7-.4 1-.2 1.1.4 2.3.6 3.6.6.6 0 1 .4 1 1V20c0 .6-.4 1-1 1A17 17 0 0 1 3 4c0-.6.4-1 1-1h3.5c.6 0 1 .4 1 1 0 1.3.2 2.5.6 3.6.1.3 0 .7-.2 1z"/></svg>
          555 214-3086
        </li>
        <li>
          <svg viewBox="0 0 24 24" aria-hidden="true"><path d="M7 1h10a2 2 0 0 1 2 2v18a2 2 0 0 1-2 2H7a2 2 0 0 1-2-2V3a2 2 0 0 1 2-2zm0 3v14h10V4zm5 15.5a1 1 0 1 0 0 2 1 1 0 0 0 0-2z"/></svg>
          555 730-4412
        </li>
        <li>
          <svg viewBox="0 0 24 24" aria-hidden="true"><path d="M2 5h20v14H2zm2 2v.4l8 5.4 8-5.4V7zm0 2.8V17h16V9.8l-8 5.4z"/></svg>
          info@volbreyinc.example
        </li>
        <li>
          <svg viewBox="0 0 24 24" aria-hidden="true"><path d="M12 2a10 10 0 1 0 0 20 10 10 0 0 0 0-20zm6.9 6h-2.9a15 15 0 0 0-1.4-3.9A8 8 0 0 1 18.9 8zM12 4c.8 1.2 1.5 2.5 1.9 4h-3.8c.4-1.5 1.1-2.8 1.9-4zM4.3 14a8 8 0 0 1 0-4h3.4a16 16 0 0 0 0 4zm.8 2h2.9c.3 1.4.8 2.7 1.4 3.9A8 8 0 0 1 5.1 16zM8 8H5.1a8 8 0 0 1 4.3-3.9C8.8 5.3 8.3 6.6 8 8zm4 12c-.8-1.2-1.5-2.5-1.9-4h3.8c-.4 1.5-1.1 2.8-1.9 4zm2.3-6H9.7a14 14 0 0 1 0-4h4.6a14 14 0 0 1 0 4zm.3 5.9c.6-1.2 1.1-2.5 1.4-3.9h2.9a8 8 0 0 1-4.3 3.9zm1.7-5.9a16 16 0 0 0 0-4h3.4a8 8 0 0 1 0 4z"/></svg>
          <span>www.<span class="web-accent">volbreyinc</span>.example</span>
        </li>
      </ul>
      <address class="address">418 Harlow Bend,<br>Tallow Creek, QA 48199</address>
    </div>

    <svg class="bottom-band" viewBox="0 0 580 26" aria-hidden="true">
      <polygon points="0,0 500,0 528,0 540,9 552,0 578,0 580,2 580,26 0,26" fill="var(--brand-red)"/>
      <line x1="542" y1="25" x2="560" y2="7" stroke="var(--paper)" stroke-width="3"/>
      <line x1="556" y1="25" x2="574" y2="7" stroke="var(--paper)" stroke-width="3"/>
    </svg>
  </section>

  <section class="card card-back" aria-label="Business card back">
    <div class="back-wordmark">VOLBREY</div>
  </section>
</main>
</body>
</html>
```